Design a logo and an adult website to upload our amateur mature milf videos filmed on Maui*

Aloha,

We need a website and a logo design for my adult website, we have a domain already. Sirenablush.com via Netkite, We are based on the island of Maui, Hawaii. We'd like to feature the word "Filmed in Tropical Locations" instead of Maui though. We want to upload amateur solo girl videos and would like to have customers be able to be driven to our site to view short clips and then become members via a monthly membership. We'd also like to be able to have an area where we can post links to items that the customer can purchase that I can wear, use, etc. I'm new to all of this, so you'll have your work cut out for you. I'm open to more suggestions. The genre for my videos is amateur mature milf.

Thank you so much!
Updates

Target Market(s)

anyone interested in mature amateur milf videos

Industry/Entity Type

Adult

Coding

Coded - Design and coding required

Number of Pages Required

1 page

Font styles to use
Script

Requirements
Must have
• able to upload many videos; membership area; store area for customers to buy me toys, costumes and outfits to wear on camera; sneak peak area to view short clips for free. Area for still photos. Categories for videos: Outdoor videos; Naughty Costumes; Slutty Whore-Shoes;
Nice to have
• I like black and hot pink as colors, but I am very open to your ideas and designs. I'm a flashy, rhinestone and hot pink kinda girl, fyi. Let's keep it fun and sexy! :)

For the logo I would like pink kiss lips next to the lettering Sirena Blush. I have uploaded a sample of what I designed. It says .com in it, but please remove that part. Thanks!
Should not have
• Please do not use Maui or Hawaii. I don't want people to know where I reside. Please use the words Exotic tropical locations, instead.

```html
<!DOCTYPE html>
<html lang="en">
<head>
<meta charset="utf-8">
<title>Sirena Blush</title>
<link rel="stylesheet" href="https://fonts.googleapis.com/css2?family=Dancing+Script:wght@600;700&family=Open+Sans:wght@400;600;700&display=swap">
<style>
:root{
  --pink:#ec1a7e;
  --pink-deep:#c9106a;
  --ink:#0d1320;
  --ink-soft:#1c2331;
  --white:#ffffff;
  --text:#4a4a4a;
  --muted:#8a8a8a;
  --line:#d9d9d9;
  --sand:#d9c2a6;
  --sea:#5a9fb8;
  --sky:#a9c8da;
  --glitter:#c9c9cc;
  --bokeh-a:#7a3c6c;
  --bokeh-b:#c6679a;
  --gold:#f4c21b;
  --script:"Dancing Script",cursive;
  --sans:"Open Sans",Arial,sans-serif;
}
*{box-sizing:border-box;margin:0;padding:0}
html,body{width:1200px;height:5140px;overflow:hidden}
body{background:var(--white);font-family:var(--sans);color:var(--text);position:relative}
.section{position:absolute;left:0;width:1200px}
.wave{position:absolute;left:0;width:1200px;display:block}
.title{font-family:var(--script);font-weight:700;color:var(--pink);font-size:52px;text-align:center;line-height:1}
.title.dark{color:var(--ink)}
.btn{display:inline-block;border-radius:20px;font-family:var(--sans);font-weight:700;font-size:13px;text-transform:uppercase;letter-spacing:.5px}
.btn-dark{background:var(--ink);color:var(--white);padding:10px 22px;font-size:14px;text-transform:none;letter-spacing:0}
.btn-pink{background:var(--pink);color:var(--white);padding:10px 22px}
.center{text-align:center}

/* header */
.header{top:0;height:120px;background:rgba(13,19,32,.92);z-index:3}
.brand{position:absolute;left:146px;top:16px;display:flex;align-items:center;gap:12px}
.brand-dot{width:34px;height:34px;border-radius:50%;background:var(--pink)}
.brand-name{font-family:var(--script);font-weight:700;font-size:36px;color:var(--pink)}
.search{position:absolute;left:456px;top:18px;width:290px;height:36px;border-radius:18px;background:var(--ink-soft);color:var(--white);font-size:13px;font-weight:700;padding:9px 20px}
.search svg{position:absolute;right:16px;top:10px}
.head-btn{position:absolute;top:18px;height:36px;padding:10px 20px;font-size:12px}
.cart{position:absolute;left:1012px;top:16px;width:40px;height:40px;border-radius:50%;background:var(--gold)}
.cart svg{position:absolute;left:10px;top:10px}
.nav{position:absolute;left:150px;top:78px;display:flex;gap:60px;font-family:var(--script);font-weight:700;font-size:26px;color:var(--white)}
.nav .active{color:var(--gold);border-bottom:3px solid var(--gold)}

/* hero */
.hero{top:0;height:690px;background:linear-gradient(120deg,#cfe1ec 0%,#8fbdd3 35%,#6f6253 60%,#4a3c30 100%)}
.hero-title{position:absolute;left:145px;top:280px;font-family:var(--script);font-weight:700;font-size:68px;line-height:1.05;color:var(--white)}
.slider-arrow{position:absolute;width:40px;height:40px;border-radius:50%;background:rgba(13,19,32,.6)}
.slider-arrow svg{position:absolute;left:13px;top:12px}

/* welcome */
.welcome{top:740px;height:260px}
.welcome p{width:820px;margin:30px auto 24px;text-align:center;font-size:14px;line-height:1.6}

/* upload */
.upload{top:1050px;height:500px;background:linear-gradient(100deg,#b7cfe0 0%,#7aa6c2 40%,#c7b39b 70%,#3d4c5d 100%)}
.upload-box{position:absolute;left:672px;top:180px;width:360px}
.upload-box h2{font-family:var(--script);font-weight:700;font-size:56px;color:var(--white);text-align:right}
.upload-box p{color:var(--white);font-size:13px;text-align:right;margin:8px 0 14px;line-height:1.5}
.upload-field{position:relative;height:42px;border-radius:21px;background:var(--white);font-size:14px;color:var(--text);padding:11px 20px}
.upload-field svg{position:absolute;right:18px;top:13px}

/* videos */
.videos{top:1590px;height:700px}
.pills{display:flex;justify-content:center;gap:10px;margin-top:30px}
.pill{height:38px;padding:9px 20px;border:2px solid var(--line);border-radius:19px;font-size:14px;color:var(--ink)}
.pill.on{background:var(--ink);color:var(--white);border-color:var(--ink)}
.grid4{position:absolute;left:144px;width:912px;display:grid;grid-template-columns:repeat(4,216px);gap:16px}
.card .shot{position:relative;height:164px;background:linear-gradient(135deg,var(--sea),var(--sand))}
.card .shot.warm{background:linear-gradient(135deg,#8a6a55,#cfae8f)}
.card .shot.blue{background:linear-gradient(135deg,#3f8fa7,#9dd0d8)}
.card .cap{background:var(--pink);color:var(--white);font-size:14px;text-align:center;height:36px;line-height:36px}
.play{position:absolute;left:86px;top:60px;width:44px;height:44px;border-radius:50%;background:rgba(255,255,255,.85)}
.play svg{position:absolute;left:16px;top:13px}
.tag{position:absolute;right:6px;top:6px;background:var(--pink);color:var(--white);font-size:10px;font-weight:700;padding:2px 6px}

/* membership */
.membership{top:2340px;height:760px;background:linear-gradient(135deg,#d8d8db 0%,#a9a9ae 30%,#e7e7ea 55%,#9d9da3 80%,#cfcfd3 100%)}
.plans{position:absolute;left:148px;top:150px;display:flex;gap:10px}
.plan{width:294px;height:506px;background:var(--white);text-align:center;padding-top:28px}
.plan h3{font-family:var(--script);font-weight:700;font-size:48px;color:var(--pink);line-height:1}
.price{width:200px;height:74px;margin:16px auto 22px;border-radius:37px;background:var(--ink);color:var(--white);font-size:40px;line-height:74px}
.plan li{list-style:none;font-size:14px;color:var(--text);padding:12px 0;border-bottom:1px solid #eee;width:230px;margin:0 auto}
.plan li.soft{color:#aaa}
.plan .btn-pink{margin-top:24px}

/* store */
.store{top:3200px;height:420px}
.store .grid4{top:150px;gap:24px;grid-template-columns:repeat(4,210px);left:150px}
.product .shot{height:164px}
.product .name{text-align:center;font-size:13px;padding:10px 0;box-shadow:0 4px 10px rgba(0,0,0,.12);background:var(--white)}
.side-arrow{position:absolute;top:230px}

/* sneak peek */
.sneak{top:3660px;height:520px;background:radial-gradient(circle at 20% 30%,var(--bokeh-b),transparent 40%),radial-gradient(circle at 80% 70%,#e59dbd,transparent 45%),linear-gradient(135deg,var(--bokeh-a),#a34d80 50%,#5b2d55)}

/* photos */
.photos{top:4240px;height:640px}
.ph{position:absolute}

/* footer */
.footer{top:4880px;height:260px;background:var(--ink)}
.socials{position:absolute;left:0;width:1200px;top:100px;display:flex;justify-content:center;gap:14px}
.socials span{width:36px;height:36px;border-radius:50%;background:#8c93a1}
.links{position:absolute;top:158px;width:1200px;display:flex;justify-content:center;gap:14px;font-size:11px;color:#b8bdc7}
.copy{position:absolute;top:190px;width:1200px;text-align:center;font-size:11px;color:#8c93a1}
</style>
</head>
<body>

<section class="section hero" role="img" aria-label="Woman in a bikini posing on a tropical beach beside rocks">
  <h1 class="hero-title">Filmed in<br>Tropical Locations</h1>
  <span class="slider-arrow" style="left:44px;top:340px"><svg width="14" height="16" viewBox="0 0 14 16"><path d="M10 2 4 8l6 6" stroke="#fff" stroke-width="2.5" fill="none"/></svg></span>
  <span class="slider-arrow" style="left:1116px;top:340px"><svg width="14" height="16" viewBox="0 0 14 16"><path d="M4 2l6 6-6 6" stroke="#fff" stroke-width="2.5" fill="none"/></svg></span>
</section>
<svg class="wave" style="top:610px" width="1200" height="100" viewBox="0 0 1200 100"><path d="M0 40 C300 90 700 95 1200 20 L1200 100 L0 100Z" fill="#fff"/><path d="M0 40 C300 90 700 95 1200 20 L1200 34 C700 108 300 104 0 56Z" fill="var(--pink)"/></svg>

<header class="section header">
  <div class="brand"><span class="brand-dot"></span><span class="brand-name">Sirena Blush</span></div>
  <div class="search">SEARCH<svg width="16" height="16" viewBox="0 0 16 16"><circle cx="7" cy="7" r="5" stroke="#fff" stroke-width="2" fill="none"/><path d="M11 11l4 4" stroke="#fff" stroke-width="2"/></svg></div>
  <span class="btn btn-pink head-btn" style="left:764px">Register Now</span>
  <span class="btn btn-pink head-btn" style="left:884px">Member Login</span>
  <span class="cart"><svg width="20" height="20" viewBox="0 0 20 20"><path d="M2 3h3l2 9h9l2-7H6" stroke="#0d1320" stroke-width="2" fill="none"/><circle cx="8" cy="16" r="1.6" fill="#0d1320"/><circle cx="15" cy="16" r="1.6" fill="#0d1320"/></svg></span>
  <nav class="nav"><span class="active">Videos</span><span>Products</span><span>Girls</span><span>Locations</span><span>Upload Video</span><span>Support</span><span>FAQ</span></nav>
</header>

<section class="section welcome">
  <h2 class="title">Welcome to Sirena Blush</h2>
  <p>Vivamus lectus justo, ultrices nec erat in, euismod iaculis mauris. Vivamus eleifend vitae nulla vel malesuada, in ac malesuada lacus, et consectetur ante. Fusce vitae lectus sit amet mi pulvinar maximus. Aenean placerat, nibh vel accumsan aliquet, magna nibh accumsan nibh, ac tempus nunc ipsum ac tellus. Cras augue magna, placerat eget nulla non, congue suscipit neque.</p>
  <div class="center"><span class="btn btn-dark">Read More</span></div>
</section>

<section class="section upload" role="img" aria-label="Woman in a white bikini standing in shallow ocean water">
  <div class="upload-box">
    <h2>Upload Videos</h2>
    <p>Etiam vel massa elementum, bibendum tellus venenatis, feugiat massa. Curabitur venenatis lacinia ornare fusce sed sollicitudin cursus dui eu placerat.</p>
    <div class="upload-field">Upload your video<svg width="18" height="16" viewBox="0 0 18 16"><path d="M1 3h6l2 2h8v10H1Z" fill="#0d1320"/></svg></div>
  </div>
</section>
<svg class="wave" style="top:1470px" width="1200" height="90" viewBox="0 0 1200 90"><path d="M0 20 C400 90 800 80 1200 10 L1200 90 L0 90Z" fill="#fff"/></svg>

<section class="section videos">
  <h2 class="title">Videos</h2>
  <div class="pills"><span class="pill on">All</span><span class="pill">Outdoor</span><span class="pill">Naughty Costumes</span><span class="pill">Slutty Whore-Shoes</span><span class="pill">Mature</span><span class="pill">Milf</span><span class="pill">More ▾</span></div>
  <div class="grid4" style="top:170px">
    <div class="card"><div class="shot warm" role="img" aria-label="Video still of a model indoors"><span class="play"><svg width="14" height="18" viewBox="0 0 14 18"><path d="M0 0l14 9-14 9Z" fill="var(--pink)"/></svg></span></div><div class="cap">Fusce eget</div></div>
    <div class="card"><div class="shot" role="img" aria-label="Video still of a model on the beach"><span class="play"><svg width="14" height="18" viewBox="0 0 14 18"><path d="M0 0l14 9-14 9Z" fill="var(--pink)"/></svg></span></div><div class="cap">Etiam vel</div></div>
    <div class="card"><div class="shot blue" role="img" aria-label="Video still of a model in a pool"><span class="play"><svg width="14" height="18" viewBox="0 0 14 18"><path d="M0 0l14 9-14 9Z" fill="var(--pink)"/></svg></span><span class="tag">FREE</span></div><div class="cap">Nulla facilis</div></div>
    <div class="card"><div class="shot" role="img" aria-label="Video still of a model by the sea"><span class="play"><svg width="14" height="18" viewBox="0 0 14 18"><path d="M0 0l14 9-14 9Z" fill="var(--pink)"/></svg></span></div><div class="cap">Etiam mattis</div></div>
    <div class="card"><div class="shot blue" role="img" aria-label="Video still of a model at the shore"><span class="play"><svg width="14" height="18" viewBox="0 0 14 18"><path d="M0 0l14 9-14 9Z" fill="var(--pink)"/></svg></span></div><div class="cap">Maecenas</div></div>
    <div class="card"><div class="shot" role="img" aria-label="Video still of a model on sand"><span class="play"><svg width="14" height="18" viewBox="0 0 14 18"><path d="M0 0l14 9-14 9Z" fill="var(--pink)"/></svg></span><span class="tag">FREE</span></div><div class="cap">Vivamus</div></div>
    <div class="card"><div class="shot warm" role="img" aria-label="Video still of a model in a bedroom"><span class="play"><svg width="14" height="18" viewBox="0 0 14 18"><path d="M0 0l14 9-14 9Z" fill="var(--pink)"/></svg></span></div><div class="cap">Aliquam</div></div>
    <div class="card"><div class="shot warm" role="img" aria-label="Video still of a model posing"><span class="play"><svg width="14" height="18" viewBox="0 0 14 18"><path d="M0 0l14 9-14 9Z" fill="var(--pink)"/></svg></span></div><div class="cap">Cras eget</div></div>
  </div>
  <div class="center" style="position:absolute;top:626px;width:1200px"><span class="btn btn-dark">View All</span></div>
</section>

<section class="section membership" role="img" aria-label="Silver glitter background">
  <h2 class="title dark" style="padding-top:72px">Membership</h2>
  <div class="plans">
    <div class="plan"><h3>Silver</h3><div class="price">$25.00</div><ul><li>Proin a dolor mauris faucibus</li><li>Vestibulum ante ipsum</li><li>Integer massa lacinia lacinia</li><li class="soft">Aenean sed quam</li><li class="soft">Vivamus interdum sapien</li><li class="soft">Duis auctor sapien</li></ul><span class="btn btn-pink">Register Now</span></div>
    <div class="plan"><h3>Gold</h3><div class="price">$35.00</div><ul><li>Proin a dolor mauris faucibus</li><li>Vestibulum ante ipsum</li><li>Integer massa lacinia lacinia</li><li>Aenean sed quam</li><li class="soft">Vivamus interdum sapien</li><li class="soft">Duis auctor sapien</li></ul><span class="btn btn-pink">Register Now</span></div>
    <div class="plan"><h3>Platinum</h3><div class="price">$45.00</div><ul><li>Proin a dolor mauris faucibus</li><li>Vestibulum ante ipsum</li><li>Integer massa lacinia lacinia</li><li>Aenean sed quam</li><li>Vivamus interdum sapien</li><li>Duis auctor sapien</li></ul><span class="btn btn-pink">Register Now</span></div>
  </div>
</section>
<svg class="wave" style="top:3000px" width="1200" height="110" viewBox="0 0 1200 110"><path d="M0 30 C300 100 800 100 1200 10 L1200 110 L0 110Z" fill="#fff"/><path d="M0 30 C300 100 800 100 1200 10 L1200 26 C800 118 300 116 0 46Z" fill="var(--pink)"/></svg>

<section class="section store">
  <h2 class="title dark">Store</h2>
  <div class="pills"><span class="pill on">All</span><span class="pill">Sex Toys</span><span class="pill">Costumes</span><span class="pill">Outfits</span></div>
  <svg class="side-arrow" style="left:52px" width="20" height="30" viewBox="0 0 20 30"><path d="M16 3 4 15l12 12" stroke="#333" stroke-width="4" fill="none"/></svg>
  <svg class="side-arrow" style="left:1124px" width="20" height="30" viewBox="0 0 20 30"><path d="M4 3l12 12L4 27" stroke="#333" stroke-width="4" fill="none"/></svg>
  <div class="grid4">
    <div class="product"><div class="shot" role="img" aria-label="Red and black lingerie" style="background:linear-gradient(135deg,#b3122d,#2a0c12)"></div><div class="name">Nullam accumsan</div></div>
    <div class="product"><div class="shot" role="img" aria-label="Purple toy on a blue background" style="background:linear-gradient(135deg,#2e6fa8,#b23aa6)"></div><div class="name">Mauris suscipit</div></div>
    <div class="product"><div class="shot" role="img" aria-label="Purple beaded accessory" style="background:linear-gradient(135deg,#2c1a3a,#8a3fa0)"></div><div class="name">Nam in tortor</div></div>
    <div class="product"><div class="shot" role="img" aria-label="Red lace costume" style="background:linear-gradient(135deg,#7d0f1c,#c62436)"></div><div class="name">Nam fringilla</div></div>
  </div>
</section>

<section class="section sneak" role="img" aria-label="Pink and purple bokeh sparkle background">
  <h2 class="title dark" style="padding-top:84px">Sneak Peak</h2>
  <svg class="side-arrow" style="left:52px;top:236px" width="20" height="30" viewBox="0 0 20 30"><path d="M16 3 4 15l12 12" stroke="#fff" stroke-width="4" fill="none"/></svg>
  <svg class="side-arrow" style="left:1124px;top:236px" width="20" height="30" viewBox="0 0 20 30"><path d="M4 3l12 12L4 27" stroke="#fff" stroke-width="4" fill="none"/></svg>
  <div class="grid4" style="top:160px">
    <div class="card"><div class="shot" role="img" aria-label="Clip preview of a model on the beach"><span class="play"><svg width="14" height="18" viewBox="0 0 14 18"><path d="M0 0l14 9-14 9Z" fill="var(--pink)"/></svg></span></div><div class="cap">Fusce eget</div></div>
    <div class="card"><div class="shot blue" role="img" aria-label="Clip preview of a model in the sea"><span class="play"><svg width="14" height="18" viewBox="0 0 14 18"><path d="M0 0l14 9-14 9Z" fill="var(--pink)"/></svg></span></div><div class="cap">Etiam vel</div></div>
    <div class="card"><div class="shot warm" role="img" aria-label="Clip preview of a model posing"><span class="play"><svg width="14" height="18" viewBox="0 0 14 18"><path d="M0 0l14 9-14 9Z" fill="var(--pink)"/></svg></span></div><div class="cap">Nulla facilis</div></div>
    <div class="card"><div class="shot" role="img" aria-label="Clip preview of a model at the shore"><span class="play"><svg width="14" height="18" viewBox="0 0 14 18"><path d="M0 0l14 9-14 9Z" fill="var(--pink)"/></svg></span></div><div class="cap">Etiam mattis</div></div>
  </div>
</section>
<svg class="wave" style="top:4100px" width="1200" height="90" viewBox="0 0 1200 90"><path d="M0 50 C400 -10 800 90 1200 30 L1200 90 L0 90Z" fill="#fff"/></svg>

<section class="section photos">
  <h2 class="title">Photos</h2>
  <div class="ph" role="img" aria-label="Model in a bikini on a beach with ocean behind" style="left:144px;top:80px;width:516px;height:192px;background:linear-gradient(180deg,#8fc3e0,#5aa3c4 55%,#d9c2a6)"></div>
  <div class="ph" role="img" aria-label="Model lying on the sand" style="left:144px;top:288px;width:236px;height:200px;background:linear-gradient(180deg,#7fb8d4,#e0ccb0)"></div>
  <div class="ph" role="img" aria-label="Model kneeling at the water's edge" style="left:388px;top:288px;width:272px;height:200px;background:linear-gradient(180deg,#6ab0cc,#d6bfa2)"></div>
  <div class="ph" role="img" aria-label="Model standing on a beach facing the sea" style="left:668px;top:80px;width:388px;height:408px;background:linear-gradient(180deg,#a9d2ea,#4f9ebf 45%,#e4d3ba)"></div>
  <div class="center" style="position:absolute;top:524px;width:1200px"><span class="btn btn-dark">View All</span></div>
</section>

<svg class="wave" style="top:4820px;z-index:2" width="1200" height="100" viewBox="0 0 1200 100"><path d="M0 30 C300 90 800 100 1200 40 L1200 100 L0 100Z" fill="var(--ink)"/><path d="M0 30 C300 90 800 100 1200 40 L1200 56 C800 116 300 106 0 46Z" fill="var(--pink)"/></svg>
<footer class="section footer">
  <div class="socials"><span></span><span></span><span></span><span></span></div>
  <div class="links"><span>Home</span><span>|</span><span>Videos</span><span>|</span><span>Products</span><span>|</span><span>Girls</span><span>|</span><span>Locations</span><span>|</span><span>Upload Video</span><span>|</span><span>Support</span><span>|</span><span>FAQ</span><span>|</span><span>Member Login</span><span>|</span><span>Register Now</span><span>|</span><span>My Cart</span><span>|</span><span>Privacy</span><span>|</span><span>Terms</span><span>|</span><span>About Us</span></div>
  <div class="copy">Copyright © 2024 Sirena Blush. All rights reserved.</div>
</footer>

</body>
</html>
```